Specialised investor in e-mobility and energy wants business card design

We need a business card design that fits our existing corporate design. <The look and feel must be 'sharp'/'clean', dynamic, communicate momentum, professionalism etc (as one would imagine from a firm in the financial sector). We like the idea of a reverse-side of the card that includes the logo, and the name and contact details on the other. We expect the deliverable to be whatever format might be required to be able to get cards printed directly by a service such as kelmo press. Our website is www.zub.capital

```html
<!DOCTYPE html>
<html lang="en">
<head>
<meta charset="utf-8">
<title>Zub Capital – Business Card</title>
<link href="https://fonts.googleapis.com/css2?family=Montserrat:wght@400;500;700&display=swap" rel="stylesheet">
<style>
  :root {
    --bg: #ece9e4;
    --brand-green: #86b04a;
    --dark-green: #2f5a26;
    --text-dark: #2b2b2b;
    --card-white: #ffffff;
  }
  * { margin: 0; padding: 0; box-sizing: border-box; }
  html, body { width: 1200px; height: 960px; overflow: hidden; background: var(--bg); }
  body { position: relative; font-family: "Montserrat", sans-serif; }

  .card {
    position: absolute;
    width: 560px; height: 320px;
    border-radius: 26px;
    box-shadow: 0 6px 18px rgba(0,0,0,0.12);
  }

  /* Logo side */
  .card-front { left: 80px; top: 80px; background: var(--brand-green); }
  .card-front .wordmark {
    position: absolute; left: 0; right: 0; top: 118px;
    text-align: center;
    color: var(--card-white);
    font-weight: 400; font-size: 66px; letter-spacing: 1px;
  }

  /* Details side */
  .card-back { left: 560px; top: 520px; background: var(--card-white); }
  .card-back .wordmark {
    position: absolute; left: 44px; top: 40px;
    color: var(--dark-green);
    font-weight: 400; font-size: 58px; letter-spacing: 1px;
  }
  .card-back .rule-main {
    position: absolute; left: 44px; right: 36px; top: 138px;
    height: 2px; background: var(--brand-green);
  }
  .holder { position: absolute; left: 44px; top: 168px; }
  .holder .name {
    color: var(--brand-green); font-weight: 700; font-size: 19px; letter-spacing: 0.5px;
    text-transform: uppercase;
  }
  .holder .role { color: var(--text-dark); font-size: 14px; margin-top: 2px; }
  .holder .rule-small { width: 200px; height: 2px; background: var(--brand-green); margin: 10px 0 10px; }
  .contacts { list-style: none; }
  .contacts li {
    display: flex; align-items: center; gap: 8px;
    color: var(--text-dark); font-size: 14px; line-height: 22px;
  }
  .contacts svg { width: 12px; height: 12px; fill: var(--brand-green); flex: none; }
  .company {
    position: absolute; right: 36px; top: 168px;
    text-align: right; color: var(--text-dark); font-size: 14px; line-height: 21px;
  }
</style>
</head>
<body>
  <section class="card card-front">
    <div class="wordmark">zub capital</div>
  </section>

  <section class="card card-back">
    <div class="wordmark">zub capital</div>
    <div class="rule-main"></div>

    <div class="holder">
      <div class="name">Aaron Feldkamp</div>
      <div class="role">Managing Director</div>
      <div class="rule-small"></div>
      <ul class="contacts">
        <li>
          <svg viewBox="0 0 12 12" aria-hidden="true"><path d="M2 1h3l1 3-2 1a7 7 0 0 0 3 3l1-2 3 1v3c0 1-1 1-1 1A10 10 0 0 1 1 2s0-1 1-1z"/></svg>
          +41 79555 0142
        </li>
        <li>
          <svg viewBox="0 0 12 12" aria-hidden="true"><path d="M1 3h10v7H1z M1 3l5 4 5-4" /></svg>
          aaron@zub.capital
        </li>
        <li>
          <svg viewBox="0 0 12 12" aria-hidden="true"><circle cx="6" cy="6" r="5.5"/></svg>
          www.zub.capital
        </li>
      </ul>
    </div>

    <div class="company">
      Zub Capital S.A.<br>
      Geneva, Switzerland
    </div>
  </section>
</body>
</html>
```